Corvane Paintless Dent Removal

Our company works on vehicles removing dents using a highly skilled trade which the metal is massaged out with special tools without disturbing the original paint, hence paintless dent removal. Besides keeping the paint and metal original its also very environmentally friendly since no paint or toxic fillers are used. Also we we are one of the most experienced companies in the business with 25 years

Target Market(s)

Retail Automobile consumers, Auto Dealerships and Auto Body Shops

Industry/Entity Type

Auto Repair

Contact Information for Business Card

Dale Hollister
PO Box 518 Brookmere, NY 11962
631-555-0148
corvanepdr@mailbox-example.com
website corvanepdr.example
youtube corvane paintless dent removal
25 years of experience removing Dents, Dings and Hail Damage

Font styles to use
Serif
Sans Serif

Colors

Designer to choose colors to be used in the design.

Requirements
Must have
• I do like things that are simple but classy and somewhat bold, also I like my logo so that should be somewhat important

```html
<!DOCTYPE html>
<html lang="en">
<head>
<meta charset="utf-8">
<title>Corvane Paintless Dent Removal – Business Card</title>
<link rel="stylesheet" href="https://fonts.googleapis.com/css2?family=Roboto:wght@400;500;700&display=swap">
<style>
  :root {
    --backdrop: #3a3a3c;
    --card: #1f1f21;
    --card-front: #1a1a1c;
    --emboss: #3b3b3e;
    --green: #7cc520;
    --blue: #0a4f92;
    --logo-blue: #1565b8;
    --text: #e6e6e6;
    --muted: #c9c9c9;
  }
  * { margin: 0; padding: 0; box-sizing: border-box; }
  html, body { width: 799px; height: 1200px; overflow: hidden; }
  body {
    background: var(--backdrop);
    font-family: "Roboto", Arial, sans-serif;
    position: relative;
  }
  .card {
    position: absolute;
    left: 60px;
    width: 680px;
    height: 389px;
    border-radius: 3px;
    overflow: hidden;
  }
  .card--front { top: 110px; background: var(--card-front); }
  .card--back { top: 700px; background: var(--card); }

  .front-brand {
    position: absolute;
    inset: 0;
    display: flex;
    flex-direction: column;
    align-items: center;
    justify-content: center;
    color: var(--emboss);
    font-weight: 700;
    text-align: center;
  }
  .front-brand__name { font-size: 66px; letter-spacing: 1px; line-height: 1; }
  .front-brand__trade { font-size: 30px; margin-top: 6px; }

  .back-brand {
    position: absolute;
    top: 28px;
    left: 0;
    right: 0;
    text-align: center;
    color: var(--logo-blue);
    font-weight: 700;
  }
  .back-brand__name { font-size: 50px; line-height: 1; letter-spacing: 1px; }
  .back-brand__trade { font-size: 22px; margin-top: 4px; }

  .holder { position: absolute; left: 40px; top: 158px; }
  .holder__name { color: var(--green); font-size: 30px; font-weight: 700; }
  .holder__role { color: var(--text); font-size: 15px; margin-top: 4px; }
  .holder__tagline { color: var(--text); font-size: 14px; line-height: 1.35; margin-top: 26px; }

  .contact {
    position: absolute;
    left: 400px;
    top: 176px;
    color: var(--text);
    font-size: 15px;
    list-style: none;
  }
  .contact li { display: flex; align-items: center; gap: 9px; line-height: 1.45; }
  .contact .address { margin-bottom: 6px; padding-left: 23px; line-height: 1.25; }
  .contact svg { width: 14px; height: 14px; fill: var(--green); flex: none; }

  .bands { position: absolute; inset: 0; width: 680px; height: 389px; }
  .bands .band-green { fill: var(--green); }
  .bands .band-blue { fill: var(--blue); }

  .channel {
    position: absolute;
    left: 342px;
    top: 341px;
    display: flex;
    align-items: center;
    gap: 10px;
    color: #fff;
    font-size: 17px;
  }
  .channel__mark { width: 16px; height: 12px; background: #fff; border-radius: 2px; }
</style>
</head>
<body>
  <section class="card card--front" aria-label="Card front">
    <div class="front-brand">
      <span class="front-brand__name">CORVANE</span>
      <span class="front-brand__trade">Paintless Dent Removal</span>
    </div>
  </section>

  <section class="card card--back" aria-label="Card back">
    <svg class="bands" viewBox="0 0 680 389" aria-hidden="true">
      <polygon class="band-green" points="0,318 316,318 298,334 0,334"/>
      <polygon class="band-blue" points="326,318 680,318 680,389 254,389"/>
    </svg>

    <div class="back-brand">
      <div class="back-brand__name">CORVANE</div>
      <div class="back-brand__trade">Paintless Dent Removal</div>
    </div>

    <div class="holder">
      <div class="holder__name">Dale Hollister</div>
      <div class="holder__role">Managing Director</div>
      <p class="holder__tagline">25 years of experience removing<br>Dents, Dings and Hail Damage</p>
    </div>

    <ul class="contact">
      <li class="address">PO Box 518 Brookmere,<br>NY 11962</li>
      <li>
        <svg viewBox="0 0 16 16" aria-hidden="true"><path d="M3 1h3l1.5 4-2 1.2a9 9 0 0 0 4.3 4.3L11 8.5l4 1.5v3a2 2 0 0 1-2 2A12 12 0 0 1 1 3a2 2 0 0 1 2-2z"/></svg>
        631-555-0148
      </li>
      <li>
        <svg viewBox="0 0 16 16" aria-hidden="true"><path d="M1 3h14v10H1z M1.5 3.5 8 9l6.5-5.5" stroke="#1f1f21" stroke-width="1.2"/></svg>
        corvanepdr@mailbox-example.com
      </li>
      <li>
        <svg viewBox="0 0 16 16" aria-hidden="true"><circle cx="8" cy="8" r="7"/><path d="M1 8h14M8 1c-3 3-3 11 0 14M8 1c3 3 3 11 0 14" stroke="#1f1f21" stroke-width="1" fill="none"/></svg>
        www.corvanepdr.example
      </li>
    </ul>

    <div class="channel">
      <span class="channel__mark" aria-hidden="true"></span>
      videohub.example/Dale Hollister
    </div>
  </section>
</body>
</html>
```